Frostvale Harborline LLC

we need a business card design

Industry/Entity Type

hvac

Contact Information for Business Card

my logo

Requirements
Must have
• my logo and same colors

```html
<!DOCTYPE html>
<html lang="en">
<head>
<meta charset="utf-8">
<title>Frostvale Harborline LLC – Business Card</title>
<link href="https://fonts.googleapis.com/css2?family=Montserrat:wght@400;500;700&display=swap" rel="stylesheet">
<style>
  :root {
    --brand-blue: #1a5fa8;
    --sky-blue: #1aa9e0;
    --gold: #f3b13c;
    --ink: #222222;
    --card: #ffffff;
    --backdrop: #e9eaec;
  }
  * { box-sizing: border-box; margin: 0; padding: 0; }
  html, body { width: 1200px; height: 689px; overflow: hidden; }
  body {
    background: var(--backdrop);
    font-family: "Montserrat", sans-serif;
    color: var(--ink);
    display: flex;
    align-items: center;
    justify-content: center;
    gap: 40px;
  }
  .card {
    width: 540px;
    height: 309px;
    background: var(--card);
    border-radius: 22px;
    box-shadow: 0 6px 20px rgba(0,0,0,0.12);
    position: relative;
  }
  .brand-mark {
    display: flex;
    align-items: center;
    gap: 10px;
    color: var(--brand-blue);
    font-weight: 700;
    text-transform: uppercase;
    letter-spacing: 0.02em;
    line-height: 1.15;
  }
  .brand-mark .mark-square {
    flex: none;
    background: var(--gold);
  }
  .card-front {
    display: flex;
    align-items: center;
    justify-content: center;
  }
  .card-front .brand-mark { font-size: 30px; }
  .card-front .mark-square { width: 34px; height: 34px; }

  .card-back .brand-mark {
    position: absolute;
    top: 46px;
    left: 150px;
    font-size: 19px;
  }
  .card-back .mark-square { width: 22px; height: 22px; }

  .person {
    position: absolute;
    left: 40px;
    top: 196px;
    width: 215px;
    text-align: right;
  }
  .person-name {
    color: var(--brand-blue);
    font-weight: 700;
    font-size: 25px;
    letter-spacing: 0.01em;
  }
  .person-role {
    font-size: 14px;
    font-weight: 400;
    margin-top: 2px;
  }
  .divider {
    position: absolute;
    left: 272px;
    top: 160px;
    width: 2px;
    height: 72px;
    background: var(--brand-blue);
  }
  .contact-list {
    position: absolute;
    left: 290px;
    top: 160px;
    list-style: none;
    font-size: 14px;
  }
  .contact-list li {
    display: flex;
    align-items: center;
    gap: 8px;
    height: 24px;
  }
  .contact-list svg { width: 12px; height: 12px; fill: var(--brand-blue); flex: none; }
  .address {
    position: absolute;
    left: 0;
    right: 0;
    bottom: 34px;
    text-align: center;
    font-size: 14px;
  }
</style>
</head>
<body>
  <section class="card card-front">
    <div class="brand-mark"><span class="mark-square"></span><span>Frostvale<br>Harborline LLC</span></div>
  </section>

  <section class="card card-back">
    <div class="brand-mark"><span class="mark-square"></span><span>Frostvale<br>Harborline LLC</span></div>

    <div class="person">
      <div class="person-name">MARCUS HALE</div>
      <div class="person-role">Managing Director</div>
    </div>

    <div class="divider"></div>

    <ul class="contact-list">
      <li>
        <svg viewBox="0 0 24 24" aria-hidden="true"><path d="M6.6 10.8a15.1 15.1 0 0 0 6.6 6.6l2.2-2.2a1 1 0 0 1 1-.25 11.4 11.4 0 0 0 3.6.57 1 1 0 0 1 1 1V20a1 1 0 0 1-1 1A17 17 0 0 1 3 4a1 1 0 0 1 1-1h3.5a1 1 0 0 1 1 1c0 1.25.2 2.45.57 3.6a1 1 0 0 1-.25 1z"/></svg>
        <span>123 456 789</span>
      </li>
      <li>
        <svg viewBox="0 0 24 24" aria-hidden="true"><path d="M2 5h20v14H2z M2 5l10 8 10-8" fill="none" stroke="#1a5fa8" stroke-width="2"/></svg>
        <span>info@frostvalehvac.com</span>
      </li>
      <li>
        <svg viewBox="0 0 24 24" aria-hidden="true"><circle cx="12" cy="12" r="10"/></svg>
        <span>www.frostvalehvac.com</span>
      </li>
    </ul>

    <p class="address">Your address, City State, Zip 1234</p>
  </section>
</body>
</html>
```